Brewlark Cup Society - A Monthly Subscription Coffee Club - Shopify Website Design

A monthly subscription company. Need a Shopify Website Design and uploaded to fully work with Tidal Renewals.

Please look at these sites for examples as well as the images I enclosed.

https://www.sipvantor.com/
https://mokrate.com/
https://www.platewinder.com/
https://www.globunchies.com/

Number of Pages Required

1 page

```html
<!DOCTYPE html>
<html lang="en">
<head>
<meta charset="utf-8">
<title>Brewlark Cup Society</title>
<link href="https://fonts.googleapis.com/css2?family=Zilla+Slab:wght@400;500;600;700&family=Lato:wght@400;700&display=swap" rel="stylesheet">
<style>
  :root {
    --paper: #ebe7e2;
    --ink: #3a2a26;
    --espresso: #3b2421;
    --muted: #7a6d67;
    --line: #d3ccc5;
    --kraft-light: #c79f76;
    --kraft-dark: #9c7452;
    --white: #ffffff;
  }
  * { box-sizing: border-box; margin: 0; padding: 0; }
  html, body { width: 1200px; height: 2704px; overflow: hidden; }
  body {
    position: relative;
    background: var(--paper);
    color: var(--ink);
    font-family: "Lato", Arial, sans-serif;
  }
  .serif { font-family: "Zilla Slab", Georgia, serif; }
  .announcement {
    position: absolute; left: 0; top: 0; width: 1200px; height: 18px;
    background: var(--espresso); color: var(--white);
    font-size: 10px; line-height: 18px; text-align: center;
  }
  .search {
    position: absolute; left: 144px; top: 66px; width: 180px;
    display: flex; align-items: center; gap: 8px;
    font-size: 13px; color: var(--muted);
    border-bottom: 1px solid var(--line); padding-bottom: 4px;
  }
  .brand {
    position: absolute; left: 0; top: 50px; width: 1200px; text-align: center;
    font-family: "Zilla Slab", Georgia, serif; font-weight: 700; font-size: 42px;
    color: var(--ink);
  }
  .header-icons { position: absolute; right: 144px; top: 66px; display: flex; gap: 18px; }
  .main-nav {
    position: absolute; left: 0; top: 140px; width: 1200px;
    display: flex; justify-content: center; gap: 40px;
    font-size: 15px; color: var(--ink);
  }
  .nav-rule { position: absolute; left: 144px; top: 180px; width: 912px; height: 1px; background: var(--line); }
  .hero {
    position: absolute; left: 144px; top: 208px; width: 912px; height: 332px;
    background: radial-gradient(ellipse at 70% 40%, #5a3a26 0%, #2a1a12 45%, #120a07 100%);
    color: var(--white); text-align: center;
  }
  .hero h1 { font-family: "Zilla Slab", Georgia, serif; font-weight: 500; font-size: 42px; margin-top: 130px; }
  .hero p { font-size: 15px; margin-top: 10px; opacity: .9; }
  .hero .btn {
    display: inline-block; margin-top: 22px; background: #8a5a3a; color: var(--white);
    font-size: 11px; letter-spacing: 1px; padding: 11px 24px;
  }
  .hero .arrow { position: absolute; top: 150px; }
  .hero .arrow.prev { left: 18px; } .hero .arrow.next { right: 18px; }
  .rule { position: absolute; left: 144px; width: 912px; height: 1px; background: var(--line); }
  .intro {
    position: absolute; left: 144px; top: 652px; width: 912px; text-align: center;
    font-family: "Zilla Slab", Georgia, serif; font-size: 25px; line-height: 40px; color: var(--ink);
  }
  .product { position: absolute; width: 260px; text-align: center; }
  .product .box {
    width: 210px; height: 170px; margin: 0 auto;
    background: linear-gradient(160deg, var(--kraft-light), var(--kraft-dark));
    border-radius: 4px;
  }
  .product h3 { font-family: "Zilla Slab", Georgia, serif; font-weight: 500; font-size: 16px; margin-top: 40px; }
  .product .price { font-size: 11px; color: var(--muted); margin-top: 6px; }
  .post { position: absolute; top: 1628px; width: 436px; }
  .post .date { text-align: center; font-size: 13px; color: var(--muted); letter-spacing: 1px; font-family: "Zilla Slab", Georgia, serif; }
  .post h2 { text-align: center; font-family: "Zilla Slab", Georgia, serif; font-weight: 500; font-size: 17px; margin-top: 10px; }
  .post .photo { width: 436px; height: 276px; margin-top: 14px; }
  .post p { font-size: 11px; line-height: 18px; color: var(--muted); margin-top: 14px; }
  .post .more { display: inline-block; font-size: 11px; margin-top: 12px; border-bottom: 1px solid var(--ink); }
  .newsletter { position: absolute; left: 0; top: 2204px; width: 1200px; text-align: center; }
  .newsletter h2 { font-family: "Zilla Slab", Georgia, serif; font-weight: 400; font-size: 34px; }
  .newsletter p { font-size: 14px; color: var(--muted); margin-top: 8px; }
  .newsletter form { display: flex; justify-content: center; gap: 8px; margin-top: 24px; }
  .newsletter .field { width: 312px; height: 40px; background: var(--white); border: 1px solid var(--line); font-size: 12px; color: var(--muted); text-align: left; padding: 12px 14px; }
  .newsletter .submit { width: 112px; height: 40px; background: var(--espresso); color: var(--white); font-size: 13px; line-height: 40px; }
  .footer-col { position: absolute; top: 2470px; }
  .footer-col h4 { font-family: "Zilla Slab", Georgia, serif; font-weight: 500; font-size: 17px; margin-bottom: 12px; }
  .footer-col li { list-style: none; font-size: 12px; line-height: 24px; }
  .footer-col p { font-size: 11px; line-height: 18px; color: var(--muted); width: 320px; margin-bottom: 10px; }
  .social { display: flex; gap: 14px; }
  .social span { width: 14px; height: 14px; border-radius: 50%; background: var(--ink); display: block; }
  .copyright { position: absolute; left: 144px; top: 2660px; font-size: 11px; color: var(--muted); }
</style>
</head>
<body>
  <div class="announcement">Free local delivery every Saturday for orders placed before Thursday noon.</div>

  <div class="search">
    <svg width="13" height="13" viewBox="0 0 13 13"><circle cx="5.5" cy="5.5" r="4.3" fill="none" stroke="#3a2a26" stroke-width="1.5"/><line x1="8.8" y1="8.8" x2="12.3" y2="12.3" stroke="#3a2a26" stroke-width="1.5"/></svg>
    Search
  </div>
  <div class="brand">Brewlark Cup Society</div>
  <div class="header-icons">
    <svg width="18" height="18" viewBox="0 0 18 18"><circle cx="9" cy="6" r="4" fill="none" stroke="#3a2a26" stroke-width="1.4"/><path d="M2 17c1-4 4-5.5 7-5.5s6 1.5 7 5.5" fill="none" stroke="#3a2a26" stroke-width="1.4"/></svg>
    <svg width="20" height="18" viewBox="0 0 20 18"><path d="M1 2h3l2 10h10l2-7H5" fill="none" stroke="#3a2a26" stroke-width="1.4"/><circle cx="8" cy="15.5" r="1.5" fill="#3a2a26"/><circle cx="15" cy="15.5" r="1.5" fill="#3a2a26"/></svg>
  </div>
  <nav class="main-nav">
    <span>Shop</span><span>Subscription</span><span>About Us &#9662;</span><span>Contact</span>
  </nav>
  <div class="nav-rule"></div>

  <section class="hero" role="img" aria-label="Roasted coffee beans scattered over a dark background">
    <svg class="arrow prev" width="16" height="24" viewBox="0 0 16 24"><path d="M12 3L4 12l8 9" fill="none" stroke="#fff" stroke-width="2.5"/></svg>
    <svg class="arrow next" width="16" height="24" viewBox="0 0 16 24"><path d="M4 3l8 9-8 9" fill="none" stroke="#fff" stroke-width="2.5"/></svg>
    <h1>Coffee Subscriptions</h1>
    <p>Donec vel ipsum ut elementum, bibendum tellus dignissim, feugiat massa</p>
    <span class="btn">SHOP NOW</span>
  </section>

  <div class="rule" style="top:592px"></div>

  <p class="intro">Vivamus lacus justo, ultrices nec erat in, euismod iaculis mauris. Vivamus eleifend vitae nulla vel malesuada. In ac malesuada lacus, et consectetur ante. Fusce vitae lectus sit amet mi pulvinar maximus. Aenean placerat, nibh vel accumsan aliquet.</p>

  <div class="rule" style="top:840px"></div>

  <div class="product" style="left:138px;top:900px"><div class="box" role="img" aria-label="Kraft subscription box with the club name printed on the lid"></div><h3>Cras sollicitudin</h3><div class="price">From $32.00</div></div>
  <div class="product" style="left:470px;top:900px"><div class="box" role="img" aria-label="Kraft subscription box with the club name printed on the lid"></div><h3>Etiam vel</h3><div class="price">From $32.00</div></div>
  <div class="product" style="left:798px;top:900px"><div class="box" role="img" aria-label="Kraft subscription box with the club name printed on the lid"></div><h3>Nulla facilisis</h3><div class="price">From $32.00</div></div>
  <div class="product" style="left:138px;top:1258px"><div class="box" role="img" aria-label="Kraft subscription box with the club name printed on the lid"></div><h3>Sed tellus</h3><div class="price">From $32.00</div></div>
  <div class="product" style="left:470px;top:1258px"><div class="box" role="img" aria-label="Kraft subscription box with the club name printed on the lid"></div><h3>Curabitur venenatis</h3><div class="price">From $32.00</div></div>
  <div class="product" style="left:798px;top:1258px"><div class="box" role="img" aria-label="Kraft subscription box with the club name printed on the lid"></div><h3>Aliquam erat</h3><div class="price">From $32.00</div></div>

  <div class="rule" style="top:1560px"></div>

  <article class="post" style="left:144px">
    <div class="date">OCTOBER 13, 2020</div>
    <h2>Fusce vitae lectus sit amet mi pulvinar maximus</h2>
    <div class="photo" role="img" aria-label="Barista weighing freshly roasted coffee beans" style="background:linear-gradient(135deg,#7a6a60,#3a2a22 55%,#b8a898)"></div>
    <p>Phasellus vitae nunc condimentum diam facilisis in, sollicitudin vel dolor. Nunc id lorem tempor lacus. Curabitur ut orci leo, in eleifend dui tellus. In scelerisque nibh porttitor mi, congue ac mauris lacinia, viverra nulla nisi.</p>
    <span class="more">Continue reading</span>
  </article>
  <article class="post" style="left:620px">
    <div class="date">OCTOBER 13, 2020</div>
    <h2>Aenean sed quam non sapien faucibus consequat</h2>
    <div class="photo" role="img" aria-label="White cup of coffee on a saucer in a warm café" style="background:radial-gradient(ellipse at 50% 70%,#e8e2da 0%,#8a5a34 40%,#3a2214 100%)"></div>
    <p>Phasellus vitae nunc condimentum diam facilisis in, sollicitudin vel dolor. Nunc id lorem tempor lacus. Curabitur ut orci leo, in eleifend dui tellus. In scelerisque nibh porttitor mi, congue ac mauris lacinia, viverra nulla nisi.</p>
    <span class="more">Continue reading</span>
  </article>

  <div class="rule" style="top:2140px"></div>

  <section class="newsletter">
    <h2>Join The Family</h2>
    <p>Sign up to our newsletter to receive updates about our future events!</p>
    <form><div class="field">Email address</div><div class="submit">Subscribe</div></form>
  </section>

  <div class="rule" style="top:2400px"></div>

  <div class="footer-col" style="left:144px">
    <h4>Social</h4>
    <div class="social"><span></span><span></span><span></span><span></span></div>
  </div>
  <div class="footer-col" style="left:452px">
    <h4>Navigation</h4>
    <ul><li>Shop</li><li>Subscription</li><li>About Us</li><li>Contact</li></ul>
  </div>
  <div class="footer-col" style="left:732px">
    <h4>Vivamus interdum</h4>
    <p>Vestibulum sodales nibh sed ante, at blandit metus sed facilisis libero. Nunc mollis ligula at nulla hendrerit vehicula.</p>
    <p>Nunc id ligula sed ante tellus nec ullamcorper.</p>
  </div>

  <div class="copyright">Copyright &copy; 2020, Brewlark Cup Society. All rights reserved.</div>
</body>
</html>
```